Company website for an international IT business

We require a website for our business, Korvel Solutions. The business has two primary areas: Lanterns, which includes two machine learning/deep learning based products and IT consultancy, which is the service we provide to other businesses.

We bridge cutting-edge research to market.

STYLING:
The site can be on single page or multi-page. This is fully open to suggestion. So long as the look and feel are consistent. Currently, we have no strong preference for colors, styles or layouts.
You can find the logo of our website in the attachment “Korvel-logo.png” and “Korvel-logo-landscape.png”.

CONTENT:
You can find the text of the website in “Website-Content.pdf”, which explains the services and products of our business. The format of the text is also open to suggestion - including breaking up the text into visually appealing sections.
We would also like to include suitable images on the website so that it does not appear to be a text-heavy page. We are happy to have placeholder images on stock image sites if needed. We are open to suggestions on placing of images

ATTACHMENT:

Industry/Entity Type

It Company

Coding

Coded - Design and coding required

Number of Pages Required

1 page

Colors

Designer to choose colors to be used in the design.

Requirements
Must have
• A full description of the requirement is in the attachment "Website-Content.pdf"
• The design must have HTML/CSS, and all resources relevant (images, fonts etc)
• We are
Nice to have
• We are open to suggestions on top of the requirement, please reach out and communicate.

```html
<!DOCTYPE html>
<html lang="en">
<head>
<meta charset="utf-8">
<title>Korvel Solutions</title>
<link rel="stylesheet" href="https://fonts.googleapis.com/css2?family=Lato:ital,wght@0,400;0,700;0,900;1,400&family=Orbitron:wght@700;800;900&display=swap">
<style>
:root{
  --blue:#1a7fc1;
  --blue-dark:#0f5f96;
  --navy:#13324d;
  --ink:#1b1b1b;
  --gray:#8a8a8a;
  --light:#f1f1f1;
  --dark:#2f3236;
  --darker:#1d2024;
  --white:#ffffff;
}
*{box-sizing:border-box;margin:0;padding:0}
html,body{width:1200px;height:4018px;overflow:hidden;background:var(--white)}
body{position:relative;font-family:"Lato",sans-serif;color:var(--ink)}
.abs{position:absolute}
.display{font-family:"Orbitron",sans-serif;font-weight:800;letter-spacing:2px}
.mark{display:inline-block;border-radius:50%;background:var(--blue)}
.pill{position:absolute;border:2px solid var(--ink);border-radius:40px;background:var(--white);font-weight:900;font-size:17px;display:flex;align-items:center;justify-content:center;text-transform:uppercase}
/* header */
.topbar{left:0;top:0;width:1200px;height:107px;background:var(--white)}
.brand{left:76px;top:13px;display:flex;align-items:center;gap:20px}
.brand .mark{width:80px;height:80px}
.brand-name{font-weight:900;font-size:28px;letter-spacing:2px;color:var(--ink)}
.info{display:flex;align-items:center;gap:14px;font-size:16px;line-height:21px}
.info .ic{width:40px;height:40px;border:2px solid var(--blue);border-radius:50%;display:flex;align-items:center;justify-content:center}
.info small{font-size:13px;font-style:italic}
.nav{left:0;top:107px;width:1200px;height:59px;background:var(--blue)}
.nav a{position:absolute;top:20px;color:#d9ecf8;font-size:16px;text-decoration:none;text-transform:uppercase}
.nav a.on{color:var(--white);font-weight:700}
.search{left:900px;top:10px;width:220px;height:38px;border-radius:20px;background:var(--navy);color:var(--white);font-size:13px;font-style:italic;padding:11px 18px}
/* hero */
.hero{left:0;top:166px;width:1200px;height:509px;background:linear-gradient(90deg,#f4f5f6 0%,#e4e8ec 35%,#8d9aa8 60%,#2e3c4d 85%,#4a5a6e 100%)}
.hero h1{left:80px;top:150px;font-weight:900;font-size:55px;line-height:64px;color:#111}
.hero p{left:80px;top:232px;font-weight:700;font-size:21px;line-height:27px;width:440px}
/* section heading */
.head{position:absolute;left:0;width:1200px;display:flex;justify-content:center;align-items:center;gap:18px;font-size:36px;font-family:"Orbitron",sans-serif;font-weight:800;letter-spacing:2px;text-transform:uppercase}
.head .mark{width:48px;height:48px}
.head b{color:var(--blue);font-weight:800}
.lead{position:absolute;text-align:center;color:var(--gray);font-size:13px;line-height:24px}
/* cards */
.card{position:absolute;background:linear-gradient(160deg,#ffffff,#eef1f4);box-shadow:0 2px 10px rgba(0,0,0,.12)}
.card h3{position:absolute;left:0;top:48px;width:100%;display:flex;justify-content:center;align-items:center;gap:12px;font-family:"Orbitron",sans-serif;font-size:21px;font-weight:800;letter-spacing:1px;text-transform:uppercase}
.card h3 .mark{width:42px;height:42px}
.card h3 b{color:var(--blue);font-weight:800}
.card p{position:absolute;left:55px;top:114px;width:394px;text-align:center;font-size:16px;line-height:27px;color:#555}
/* what */
.what{left:0;top:1506px;width:1200px;height:482px;background:linear-gradient(180deg,#3a3c40,#2b2d31)}
.svc{position:absolute;top:1746px;width:335px;height:190px;border-radius:6px;background:rgba(190,190,190,.75);text-align:center;padding-top:60px}
.svc.on{background:var(--white)}
.svc h4{font-size:21px;font-weight:400;color:#111}
.svc p{font-size:14px;line-height:19px;color:#444;margin:10px 30px 0}
.svc.on p{color:#999}
.orb{position:absolute;top:1668px;width:120px;height:120px;border-radius:50%;background:var(--white);border:4px solid #7d7d7d;display:flex;align-items:center;justify-content:center}
.orb.on{border-color:var(--navy)}
.orb i{width:80px;height:80px;border-radius:50%;background:#666;display:flex;align-items:center;justify-content:center}
.orb.on i{background:var(--blue)}
/* help */
.help{left:0;top:2406px;width:1200px;height:482px;background:var(--light)}
/* newsletter */
.news-bg{left:0;top:2888px;width:1200px;height:295px;background:linear-gradient(180deg,#25282c,#35383d 60%,#222428)}
/* news */
.post{position:absolute;top:3295px;width:247px;height:295px;background:var(--white);box-shadow:0 1px 6px rgba(0,0,0,.15)}
.post .ph{height:166px}
.post h5{margin:20px 22px 0;font-size:16px;font-weight:400;line-height:21px}
.post .meta{margin:18px 22px 0;font-size:11px;color:var(--gray);display:flex;gap:18px}
/* footer */
.foot{left:0;top:3633px;width:1200px;height:327px;background:linear-gradient(180deg,#1f2226,#2c2f33)}
.foot h6{position:absolute;top:3676px;font-family:"Orbitron",sans-serif;font-size:14px;font-weight:800;color:var(--blue);text-transform:uppercase;letter-spacing:1px}
.links{left:356px;top:3716px;list-style:none;color:#cfcfcf;font-size:14px;line-height:22.5px}
.links li::before{content:"› ";color:var(--blue)}
.links li:first-child{color:var(--white)}
.field{position:absolute;border:1px solid #8a8a8a;border-radius:20px;color:#9a9a9a;font-size:12px;padding:12px 16px}
.copy{left:0;top:3960px;width:1200px;height:58px;background:var(--blue);color:var(--white);font-size:14px;display:flex;justify-content:center;align-items:center;gap:6px}
</style>
</head>
<body>

<header>
  <div class="abs topbar"></div>
  <div class="abs brand"><span class="mark"></span><span class="brand-name">KORVEL</span></div>
  <div class="abs info" style="left:640px;top:30px">
    <span class="ic"><svg width="20" height="20" viewBox="0 0 24 24"><path d="M6.6 10.8a15 15 0 0 0 6.6 6.6l2.2-2.2a1 1 0 0 1 1-.25 11.4 11.4 0 0 0 3.6.6 1 1 0 0 1 1 1V20a1 1 0 0 1-1 1A17 17 0 0 1 3 4a1 1 0 0 1 1-1h3.5a1 1 0 0 1 1 1c0 1.25.2 2.45.6 3.6a1 1 0 0 1-.25 1z" fill="#1a7fc1"/></svg></span>
    <span>Call Today:<br>555 010 2040</span>
  </div>
  <div class="abs info" style="left:840px;top:30px">
    <span class="ic"><svg width="20" height="20" viewBox="0 0 24 24"><circle cx="12" cy="12" r="9" fill="none" stroke="#1a7fc1" stroke-width="2"/><path d="M12 7v5l3 2" stroke="#1a7fc1" stroke-width="2" fill="none"/></svg></span>
    <span>Opening Hours:<br><small>Mon-Fri : 9am-6pm; Sun : 10am-1pm</small></span>
  </div>
  <nav class="abs nav">
    <a class="on" style="left:100px">Home</a>
    <a style="left:210px">About</a>
    <a style="left:328px">Lanterns</a>
    <a style="left:465px">Consultancy</a>
    <a style="left:648px">News</a>
    <a style="left:758px">Contact</a>
    <div class="abs search">Type here...
      <svg class="abs" style="right:16px;top:11px" width="16" height="16" viewBox="0 0 24 24"><circle cx="10" cy="10" r="7" fill="none" stroke="#fff" stroke-width="3"/><path d="M15 15l6 6" stroke="#fff" stroke-width="3"/></svg>
    </div>
  </nav>
</header>

<section>
  <div class="abs hero" role="img" aria-label="Photo of two businessmen in suits reviewing a tablet in a city office">
    <h1 class="abs">KORVEL SOLUTIONS</h1>
    <p class="abs">Lorem Ipsum is simply dummy text of the printing and typesetting industry.</p>
  </div>
  <div class="pill" style="left:76px;top:477px;width:182px;height:54px;border-width:3px">Get Started</div>
</section>

<section>
  <h2 class="head" style="top:722px"><span class="mark"></span>Welcome to <b>Korvel</b></h2>
  <p class="lead" style="left:150px;top:790px;width:900px">Lorem Ipsum is simply dummy text of the printing and typesetting industry. Lorem Ipsum has been the industry's standard dummy text ever since the 1500s, when an unknown printer took a galley of type and scrambled it to make a type specimen book.Lorem Ipsum is simply dummy text of the printing and typesetting industry. Lorem Ipsum has been the industry's standard dummy text ever since the 1500s, when an unknown printer took a galley of type and scrambled it to make a type specimen book.</p>
  <div class="pill" style="left:509px;top:903px;width:182px;height:54px;border-color:var(--navy)">Read More</div>
  <svg class="abs" style="left:0;top:995px" width="1200" height="30"><defs><linearGradient id="fade" x1="0" x2="1"><stop offset="0" stop-color="#ddd" stop-opacity="0"/><stop offset=".5" stop-color="#bbb"/><stop offset="1" stop-color="#ddd" stop-opacity="0"/></linearGradient></defs><path d="M150 12H580L600 28L620 12H1050" fill="none" stroke="url(#fade)" stroke-width="2"/></svg>

  <article class="card" style="left:80px;top:1058px;width:504px;height:381px">
    <h3><span class="mark"></span>Korvel <b>Lanterns</b></h3>
    <p>Lorem Ipsum is simply dummy text of the printing and typesetting industry. Lorem Ipsum has been the industry's standard dummy text ever since the 1500s, when an unknown printer took a galley of type and scrambled it to make a type specimen book.</p>
    <div class="pill" style="left:160px;top:272px;width:182px;height:54px;border-color:var(--navy)">Read More</div>
  </article>
  <article class="card" style="left:616px;top:1058px;width:504px;height:381px">
    <h3><span class="mark"></span>Korvel <b>Consultancy</b></h3>
    <p>Lorem Ipsum is simply dummy text of the printing and typesetting industry. Lorem Ipsum has been the industry's standard dummy text ever since the 1500s, when an unknown printer took a galley of type and scrambled it to make a type specimen book.</p>
    <div class="pill" style="left:160px;top:268px;width:182px;height:54px;border-color:var(--navy)">Read More</div>
  </article>
</section>

<section>
  <div class="abs what" role="img" aria-label="Dimmed photo of an office workspace"></div>
  <h2 class="head" style="top:1556px;color:var(--white)"><span class="mark"></span>What is <b>Korvel</b></h2>
  <p class="lead" style="left:200px;top:1618px;width:800px;color:#e6e6e6;font-size:15px">Korvel Solutions is an IT consultancy firm with a diffrence.We can provide IT expertise for your business at any stage - from intial idea to live system.</p>
  <div class="svc" style="left:75px"><h4>Software Development</h4><p>Lorem Ipsum is simply dummy text of the printing and typesetting industry. Lorem Ipsum has been the industry's standard...</p></div>
  <div class="svc on" style="left:434px"><h4>IOT System Design</h4><p>Lorem Ipsum is simply dummy text of the printing and typesetting industry. Lorem Ipsum has been the industry's standard...</p></div>
  <div class="svc" style="left:791px"><h4>Machine learning solutions</h4><p>Lorem Ipsum is simply dummy text of the printing and typesetting industry. Lorem Ipsum has been the industry's standard...</p></div>
  <div class="orb" style="left:182px"><i><svg width="44" height="36" viewBox="0 0 44 36"><rect x="2" y="2" width="40" height="32" rx="3" fill="none" stroke="#fff" stroke-width="3"/><path d="M2 10H42M17 17l-5 5 5 5M27 17l5 5-5 5" fill="none" stroke="#fff" stroke-width="2.5"/></svg></i></div>
  <div class="orb on" style="left:540px"><i><svg width="40" height="40" viewBox="0 0 40 40"><circle cx="20" cy="20" r="8" fill="#fff"/><g stroke="#fff" stroke-width="2"><path d="M20 2v8M20 30v8M2 20h8M30 20h8M7 7l6 6M27 27l6 6M33 7l-6 6M13 27l-6 6"/></g></svg></i></div>
  <div class="orb" style="left:898px"><i><svg width="40" height="40" viewBox="0 0 40 40"><circle cx="20" cy="20" r="14" fill="none" stroke="#fff" stroke-width="3"/><circle cx="20" cy="20" r="5" fill="#fff"/></svg></i></div>
</section>

<section>
  <h2 class="head" style="top:2040px"><span class="mark"></span>Testimonial</h2>
  <svg class="abs" style="left:460px;top:2156px" width="44" height="30"><rect width="44" height="30" fill="#fff" stroke="#999"/><path d="M28 15H16M21 10l-5 5 5 5" stroke="#333" stroke-width="2" fill="none"/></svg>
  <div class="abs" role="img" aria-label="Portrait of a client" style="left:553px;top:2125px;width:94px;height:94px;border-radius:50%;background:linear-gradient(180deg,#d9d9d9,#7d8894);border:4px solid #ddd"></div>
  <svg class="abs" style="left:697px;top:2156px" width="44" height="30"><rect width="44" height="30" fill="#1a7fc1"/><path d="M16 15H28M23 10l5 5-5 5" stroke="#fff" stroke-width="2" fill="none"/></svg>
  <div class="abs" style="left:128px;top:2205px;font-size:90px;color:#ccc;font-family:Georgia,serif">“</div>
  <div class="abs" style="left:1025px;top:2270px;font-size:90px;color:#ccc;font-family:Georgia,serif">”</div>
  <p class="lead" style="left:220px;top:2238px;width:760px;font-style:italic;font-size:15px;line-height:26px;color:#999">Lorem Ipsum is simply dummy text of the printing and typesetting industry. Lorem Ipsum has been the industry's standard dummy text ever since the 1500s, when an unknown printer took a galley of type and scrambled it to make a type specimen book.</p>
  <div class="abs display" style="left:0;width:1200px;top:2334px;text-align:center;color:var(--blue);font-size:16px">LOREM IPSUM</div>
</section>

<section>
  <div class="abs help"></div>
  <h2 class="head" style="top:2458px"><span class="mark"></span>How we can <b>help</b></h2>
  <svg class="abs" style="left:155px;top:2602px" width="48" height="66" viewBox="0 0 48 66"><path d="M16 4h16l-4 10h-8z" fill="#1a3f63"/><path d="M18 16h12c12 8 18 20 18 32 0 10-8 16-24 16S0 58 0 48c0-12 6-24 18-32z" fill="#1a3f63"/><text x="24" y="52" text-anchor="middle" fill="#fff" font-family="Lato" font-weight="900" font-size="24">$</text></svg>
  <p class="abs" style="left:230px;top:2610px;width:460px;font-size:21px;line-height:30px">Avoid the overhead oncurred by frequent scaling of your development team</p>
  <p class="abs" style="left:153px;top:2688px;width:572px;font-size:15px;line-height:25px;color:#888">Lorem Ipsum is simply dummy text of the printing and typesetting industry. Lorem Ipsum has been the industry's standard dummy text ever since the 1500s, when an unknown printer took a galley of type and scrambled it to make a type specimen book.</p>
  <svg class="abs" style="left:712px;top:2545px" width="350" height="330" viewBox="0 0 350 330">
    <circle cx="175" cy="180" r="132" fill="#fff"/>
    <circle cx="175" cy="180" r="100" fill="#f0f0f0"/>
    <path d="M175 30A150 150 0 0 1 325 180" fill="none" stroke="#1a7fc1" stroke-width="6"/>
    <circle cx="175" cy="30" r="26" fill="#fff" stroke="#ddd"/>
    <path d="M161 26h18v10h-18zM179 30h6l4 6h-10z" fill="none" stroke="#333" stroke-width="2"/>
    <circle cx="48" cy="190" r="26" fill="#fff" stroke="#ddd"/>
    <path d="M35 199l8-10 6 6 12-14" fill="none" stroke="#333" stroke-width="3"/>
    <circle cx="322" cy="180" r="24" fill="#1a7fc1" stroke="#0d4a78" stroke-width="5"/>
    <text x="322" y="188" text-anchor="middle" fill="#fff" font-family="Lato" font-weight="900" font-size="22">$</text>
  </svg>
</section>

<section>
  <div class="abs news-bg" role="img" aria-label="Dark photo of a city skyline"></div>
  <h2 class="head" style="top:2938px;color:var(--white)"><span class="mark"></span>Newsletter <b>Subscription</b></h2>
  <p class="lead" style="left:300px;top:3002px;width:600px;color:#eee;font-size:15px">Lorem Ipsum is simply dummy text of the printing and typesetting industry. Lorem Ipsum has been the industry's standard dummy text.</p>
  <div class="abs" style="left:316px;top:3070px;width:563px;height:54px;border:1px solid #aaa;border-radius:30px;color:#bbb;font-size:13px;padding:18px 24px">Email</div>
  <svg class="abs" style="left:812px;top:3082px" width="34" height="30" viewBox="0 0 34 30"><path d="M2 14L32 2 26 28 16 19z" fill="#fff"/><path d="M16 19L32 2" stroke="#333" stroke-width="1.5"/></svg>
</section>

<section>
  <h2 class="head" style="top:3227px"><span class="mark"></span>Latest <b>News</b></h2>
  <article class="post" style="left:78px"><div class="ph" role="img" aria-label="Photo of a woman working on a laptop" style="background:linear-gradient(135deg,#d9c3a8,#8e6d52)"></div><h5>Lorem Ipsum is simply dummy text</h5><div class="meta"><span>By Mara Quill</span><span>10 Jan 2018</span></div></article>
  <article class="post" style="left:343px"><div class="ph" role="img" aria-label="Photo of a city at night with digital lights" style="background:linear-gradient(135deg,#2c5d86,#123050)"></div><h5>Lorem Ipsum is simply dummy text</h5><div class="meta"><span>By Mara Quill</span><span>8 Jan 2018</span></div></article>
  <article class="post" style="left:608px"><div class="ph" role="img" aria-label="Photo of a hazy city skyline" style="background:linear-gradient(135deg,#d7d2c9,#7f7b76)"></div><h5>Lorem Ipsum is simply dummy text</h5><div class="meta"><span>By Mara Quill</span><span>15 Feb 2017</span></div></article>
  <article class="post" style="left:873px"><div class="ph" role="img" aria-label="Overhead photo of a team meeting at a desk" style="background:linear-gradient(135deg,#eef1f3,#8a9aa6)"></div><h5>Lorem Ipsum is simply dummy text</h5><div class="meta"><span>By Mara Quill</span><span>15 Feb 2017</span></div></article>
</section>

<footer>
  <div class="abs foot"></div>
  <span class="abs mark" style="left:135px;top:3682px;width:100px;height:100px"></span>
  <div class="abs" style="left:85px;top:3790px;width:200px;text-align:center;font-weight:900;font-size:28px;letter-spacing:2px;color:var(--white)">KORVEL</div>
  <span class="abs mark" style="left:93px;top:3844px;width:44px;height:44px"></span>
  <span class="abs mark" style="left:160px;top:3844px;width:44px;height:44px;background:none;border:2px solid #fff"></span>
  <span class="abs mark" style="left:222px;top:3844px;width:44px;height:44px;background:none;border:2px solid #fff"></span>
  <h6 style="left:356px">Quick Links</h6>
  <ul class="abs links"><li>Home</li><li>About Us</li><li>Lanterns</li><li>Consultancy</li><li>Testimonials</li><li>News</li><li>Contact Us</li></ul>
  <h6 style="left:536px">Contact Info</h6>
  <svg class="abs" style="left:534px;top:3712px" width="22" height="28" viewBox="0 0 22 28"><path d="M11 0a11 11 0 0 1 11 11c0 8-11 17-11 17S0 19 0 11A11 11 0 0 1 11 0z" fill="#1a7fc1"/><circle cx="11" cy="11" r="4" fill="#2c2f33"/></svg>
  <div class="abs" style="left:564px;top:3714px;color:#fff;font-weight:900;font-size:15px;letter-spacing:1px">KORVEL</div>
  <div class="abs" style="left:564px;top:3738px;color:#ccc;font-size:13px;line-height:19px;width:150px">48 Harbor Lane,<br>Westfield 20415</div>
  <svg class="abs" style="left:534px;top:3814px" width="22" height="22" viewBox="0 0 24 24"><path d="M6.6 10.8a15 15 0 0 0 6.6 6.6l2.2-2.2a1 1 0 0 1 1-.25 11.4 11.4 0 0 0 3.6.6 1 1 0 0 1 1 1V20a1 1 0 0 1-1 1A17 17 0 0 1 3 4a1 1 0 0 1 1-1h3.5a1 1 0 0 1 1 1c0 1.25.2 2.45.6 3.6a1 1 0 0 1-.25 1z" fill="#1a7fc1"/></svg>
  <div class="abs" style="left:564px;top:3816px;color:#ddd;font-size:14px">555 010 2040</div>
  <svg class="abs" style="left:534px;top:3862px" width="22" height="16" viewBox="0 0 22 16"><rect width="22" height="16" rx="2" fill="#1a7fc1"/><path d="M1 2l10 7 10-7" stroke="#2c2f33" stroke-width="2" fill="none"/></svg>
  <div class="abs" style="left:564px;top:3862px;color:#ddd;font-size:14px">hello@korvel.example</div>
  <h6 style="left:739px">Contact Form</h6>
  <div class="field" style="left:739px;top:3714px;width:184px;height:42px">Enter Name</div>
  <div class="field" style="left:935px;top:3714px;width:185px;height:42px">Enter Email</div>
  <div class="field" style="left:739px;top:3764px;width:381px;height:82px;border-radius:18px">Message</div>
  <div class="pill" style="left:750px;top:3856px;width:156px;height:46px;border:none;font-size:15px">Submit</div>
  <div class="abs copy">© <b style="letter-spacing:2px">KORVEL</b> - 2018. All Rights Reserved</div>
</footer>

</body>
</html>
```